PWRPT design for Company

Project: Develop a pwrpt for QT7lx. This can be just a blank pwrpt with standard templates that we can use to build our content and solutions around.
Website: www.qt7lx.example
Color Pallet: Try to use the color schema from our website.
PWRPT Design Tips: While we are a research-based company, our primary target is schools and school districts. We say our work is RESEARCH, POLICY, AND PRACTICE. I would like images that represent “WHY” our research matters, i.e. students, teachers, and administrators. If you can use images and stock photos that represent students with diverse backgrounds, teachers that are diverse and clearly teaching, and administrators that run a school, university, etc. We are in the process of updating our website, but the color scheme will remain the same.
Additional Information:
We built, researched, and designed, www.brvo-kt.example .
We built, researched, and designed, http://67pwgamma.example/olar/index.html
Target Market(s)
EDUCATION
Industry/Entity Type
It Company
Look and feel

```html
<!DOCTYPE html>
<html lang="en">
<head>
<meta charset="utf-8">
<title>QT7lx — Welcome Slide</title>
<link href="https://fonts.googleapis.com/css2?family=Montserrat:wght@300;400;500;800&display=swap" rel="stylesheet">
<style>
  :root {
    --orange: #ee7a16;
    --orange-light: #f38a2a;
    --divider: #5b6166;
    --footer-bar: #4f555a;
    --ink: #3f4448;
    --muted: #8b9094;
    --white: #ffffff;
    --photo-haze: #e9e6e2;
    --photo-skin: #d9ae93;
    --photo-pink: #d98aa6;
    --photo-blue: #7f95c2;
    --photo-green: #8fcf6a;
  }
  html, body {
    margin: 0;
    padding: 0;
    overflow: hidden;
    background: var(--white);
  }
  .slide {
    position: relative;
    width: 1200px;
    height: 900px;
    overflow: hidden;
    background: var(--white);
    font-family: "Montserrat", sans-serif;
  }
  .hero {
    position: absolute;
    left: 0;
    top: 0;
    width: 1200px;
    height: 735px;
  }
  .hero-text {
    position: absolute;
    left: 667px;
    top: 528px;
    color: var(--white);
  }
  .hero-title {
    margin: 0;
    font-weight: 800;
    font-size: 54px;
    line-height: 1;
    letter-spacing: 0.3px;
  }
  .hero-program {
    margin: 12px 0 0;
    font-weight: 400;
    font-size: 39px;
    line-height: 1.1;
  }
  .hero-date {
    margin: 16px 0 0;
    font-weight: 300;
    font-size: 28px;
    line-height: 1.1;
  }
  .legal {
    position: absolute;
    left: 40px;
    top: 790px;
    width: 710px;
    margin: 0;
    font-weight: 400;
    font-size: 16.2px;
    line-height: 1.6;
    color: var(--ink);
  }
  .brand-mark {
    position: absolute;
    left: 820px;
    top: 772px;
    width: 60px;
    height: 60px;
    background: var(--orange);
  }
  .brand-name {
    position: absolute;
    left: 905px;
    top: 754px;
    font-weight: 400;
    font-size: 84px;
    line-height: 1;
    color: var(--divider);
    letter-spacing: 1px;
  }
  .brand-tagline {
    position: absolute;
    left: 908px;
    top: 851px;
    margin: 0;
    font-weight: 400;
    font-size: 13.5px;
    letter-spacing: 0.4px;
    color: var(--muted);
  }
  .footer-bar {
    position: absolute;
    left: 0;
    bottom: 0;
    width: 1200px;
    height: 18px;
    background: var(--footer-bar);
  }
</style>
</head>
<body>
  <main class="slide">
    <svg class="hero" viewBox="0 0 1200 735" xmlns="http://www.w3.org/2000/svg">
      <defs>
        <linearGradient id="photoTone" x1="0" y1="0" x2="0.35" y2="1">
          <stop offset="0" stop-color="var(--photo-haze)"/>
          <stop offset="0.35" stop-color="var(--photo-skin)"/>
          <stop offset="0.62" stop-color="var(--photo-pink)"/>
          <stop offset="0.82" stop-color="var(--photo-blue)"/>
          <stop offset="1" stop-color="var(--photo-green)"/>
        </linearGradient>
        <linearGradient id="panelTone" x1="0" y1="1" x2="1" y2="0">
          <stop offset="0" stop-color="var(--orange)"/>
          <stop offset="1" stop-color="var(--orange-light)"/>
        </linearGradient>
      </defs>
      <rect class="hero-photo" x="0" y="0" width="900" height="735" fill="url(#photoTone)"
            role="img" aria-label="Photo: a diverse group of smiling students giving thumbs up, one holding a green notebook"/>
      <polygon class="hero-panel" points="852,0 1200,0 1200,735 544,735" fill="url(#panelTone)"/>
      <line class="hero-divider" x1="851" y1="0" x2="545" y2="735" stroke="var(--divider)" stroke-width="7"/>
    </svg>

    <div class="hero-text">
      <h1 class="hero-title">WELCOME</h1>
      <p class="hero-program">Trailway2Futures (T2F)</p>
      <p class="hero-date">August 21st, 2017</p>
    </div>

    <p class="legal">© 2017 All rights reserved. Contains confidential and proprietary information and may not be disclosed or reproduced without&nbsp; the prior written consent of QT7lx</p>

    <div class="brand-mark"></div>
    <div class="brand-name">QT7lx</div>
    <p class="brand-tagline">RESEARCH + POLICY + PRACTICE</p>

    <div class="footer-bar"></div>
  </main>
</body>
</html>
```